Sophisticated, clean website reflecting my feminine, playful side to sell my abstract art,

I need a website no more than 3 pages to showcase my paintings, a little about me and some contact info. I do abstracts so looking for something a little edgy, yet feminine and current.
Updates

Hi there, These are some artists websites that I Iike: Marnelvoss.com (I like how airy it is) peterwallombry.com garethpolvens.com (I like how it scrolls) I'll need a place for a photo ( a headshot-i do not have it yet so I'll need to be able to upload that later) as well as an area for my bio. Also, it's important that I will be able to upload any new photos and descriptions easily so it should be user friendly. Lastly, I like in a sunny place so would like to have this seem upbeat and playful as that is how i like to paint. thanks-I'm trying to upload my photos now -

Target Market(s)

ppl ages 35-70 who want large scale art for their homes

Industry/Entity Type

art

Coding

Coded - Design and coding required

Number of Pages Required

3 page

Colors

Designer to choose colors to be used in the design.

Requirements
Must have
• photos of my art, a place for my bio, be easy to reach me. tasteful-nothing too "in your face" -my clients are pretty high end and organized. They like clean lines
Nice to have
• sophisticated background, muted tones in the back-similar clean font throughout-no cursive
Should not have
• too many dark areas. Too many blocks of color. Too serious.

```html
<!DOCTYPE html>
<html lang="en">
<head>
<meta charset="utf-8">
<title>Hanna Selwick — Contact</title>
<link rel="stylesheet" href="https://fonts.googleapis.com/css2?family=Oswald:wght@300;400&family=Baloo+2:wght@400&display=swap">
<style>
  :root {
    --ink: #000000;
    --paper: #ffffff;
    --muted: #8a8a8a;
    --rule: #1a1a1a;
    --sun: #f5d842;
  }
  * { box-sizing: border-box; margin: 0; padding: 0; }
  html, body { width: 1200px; height: 752px; overflow: hidden; background: var(--paper); }
  .page { position: relative; width: 1200px; height: 752px; color: var(--ink); font-family: "Baloo 2", sans-serif; }

  .brand { position: absolute; top: 25px; left: 0; width: 1200px; height: 67px; display: flex; justify-content: center; align-items: center; gap: 14px; }
  .brand-word { font-family: "Oswald", sans-serif; font-weight: 300; font-size: 15px; letter-spacing: 0.3px; text-transform: uppercase; line-height: 1; }
  .brand-mark { width: 54px; height: 67px; background: var(--ink); }
  .brand-rule { position: absolute; top: 109px; left: 514px; width: 172px; height: 1px; background: #555; }

  .nav { position: absolute; top: 132px; left: 0; width: 1200px; display: flex; justify-content: center; gap: 55px; padding-left: 0; }
  .nav a { font-family: "Oswald", sans-serif; font-weight: 300; font-size: 19px; color: var(--ink); text-decoration: none; text-transform: uppercase; line-height: 28px; }
  .nav a.is-current { color: var(--sun); }

  .contact-form { position: absolute; top: 230px; left: 391px; width: 417px; }
  .field { position: relative; border-bottom: 1px solid var(--rule); height: 33px; margin-bottom: 15px; }
  .field--message { height: 72px; margin-bottom: 30px; }
  .field-label { position: absolute; left: 16px; top: 7px; font-size: 13px; color: var(--muted); line-height: 20px; }
  .field-label .req { color: var(--ink); margin-right: 3px; }

  .send-button { display: block; width: 417px; height: 46px; border: 0; background: var(--ink); color: var(--paper); font-family: "Oswald", sans-serif; font-weight: 400; font-size: 15px; text-transform: uppercase; letter-spacing: 0.2px; }
  .form-note { margin-top: 13px; text-align: center; font-size: 11.5px; color: var(--muted); }

  .social { position: absolute; top: 574px; left: 0; width: 1200px; display: flex; justify-content: center; gap: 26px; }
  .social-link { width: 29px; height: 29px; border: 1.5px solid var(--ink); border-radius: 50%; display: block; }

  .footer { position: absolute; top: 721px; left: 0; width: 1200px; text-align: center; font-size: 11.5px; color: #222; }
</style>
</head>
<body>
<div class="page">
  <header>
    <div class="brand">
      <span class="brand-word">Hanna</span>
      <span class="brand-mark"></span>
      <span class="brand-word">Selwick</span>
    </div>
    <div class="brand-rule"></div>
    <nav class="nav">
      <a href="#">Gallery</a>
      <a href="#">About</a>
      <a href="#" class="is-current">Contact</a>
    </nav>
  </header>

  <form class="contact-form">
    <div class="field"><span class="field-label"><span class="req">*</span>First Name</span></div>
    <div class="field"><span class="field-label"><span class="req">*</span>Last Name</span></div>
    <div class="field"><span class="field-label"><span class="req">*</span>Email</span></div>
    <div class="field field--message"><span class="field-label"><span class="req">*</span>Message</span></div>
    <button type="button" class="send-button">Send Message</button>
    <p class="form-note">Fields containing (*) are mandatory.</p>
  </form>

  <div class="social" aria-label="Social links">
    <a class="social-link" href="#" aria-label="Social profile one"></a>
    <a class="social-link" href="#" aria-label="Social profile two"></a>
    <a class="social-link" href="#" aria-label="Social profile three"></a>
    <a class="social-link" href="#" aria-label="Social profile four"></a>
  </div>

  <footer class="footer">©2022 Hanna Selwick Art. All rights reserved.</footer>
</div>
</body>
</html>
```